Powerpoint design template for LUMOTEX for new digital platform

We would like to use a PowerPoint template, we would like to create a new page, we would like to create a new digital platform LUMOTEX for schools and parents for the creation of playful communication and educational tools for children to enhance their positive development, amaze them learn in a playful way. This platform is going to be the most creative, stimulating and innovative classroom, easy to use and fast to implement. Scrapbooking, collages ... Magazine, newsletters Diplomla / awards Slideshows Facebook Calendars Organizers Greetings Games ... This powerpoint template will be used essential to We are looking for a professional design, positioning our brand in the children market with an adult hearing. so you will need to find a good deal. Primary target: nurseries & schools from 0 to 18 years old and universities (in 2nd phase) Secondary target: small & medium businesses Third target: general public, and TPE If it is a color scheme, then it is suggested that it be marketed in Europe (UK, Italy, Spain) and in a 2nd Stage USA and other countries. multiple options for front page, insidious pages (multiple styles with limited text and extended text) and final contact page We need something to read, we can not do it too much, but we can not do it. , and inside pages aligned to our logo

Target Market(s)

Target 1; Education with teacher Target 2; parents and grandparents

Industry/Entity Type

Education

Font styles to use
Other font styles liked:
• not decided. but not too fancy

Requirements
Must have
• Multi page options for front page, page insides (multiple styles with limited text and extended text) and final page contact
Nice to have
• do not have a lot of ideas. We need something to read, we can not get away from it
Should not have
• not too fancy and busy: keep clarity & simplicity while reassuring on quality

```html
<!DOCTYPE html>
<html lang="en">
<head>
<meta charset="UTF-8">
<title>LUMOTEX – Content Page</title>
<link href="https://fonts.googleapis.com/css2?family=Nunito:wght@400;600;800;900&display=swap" rel="stylesheet">
<style>
  :root {
    --pink: #e6307f;
    --cyan: #0aa6e6;
    --orange: #f47b20;
    --lime: #c9d72f;
    --white: #ffffff;
    --ink: #262626;
    --brand-square: #c9d72f;
  }
  html, body {
    margin: 0;
    padding: 0;
    width: 1200px;
    height: 900px;
    overflow: hidden;
    background: var(--white);
  }
  .slide {
    position: relative;
    width: 1200px;
    height: 900px;
    overflow: hidden;
    background: var(--white);
    font-family: "Nunito", sans-serif;
  }
  .content-title {
    position: absolute;
    left: 37px;
    top: 38px;
    margin: 0;
    font-size: 43px;
    font-weight: 600;
    letter-spacing: 0.5px;
    color: var(--pink);
    line-height: 1;
  }
  .brand {
    position: absolute;
    left: 996px;
    top: 38px;
    display: flex;
    flex-direction: column;
  }
  .brand-name {
    display: flex;
    align-items: center;
    gap: 10px;
    font-size: 34px;
    font-weight: 900;
    color: var(--ink);
    line-height: 1;
  }
  .brand-square {
    width: 26px;
    height: 26px;
    background: var(--brand-square);
  }
  .brand-tagline {
    margin-top: 8px;
    margin-left: 2px;
    font-size: 10px;
    font-weight: 600;
    letter-spacing: 2px;
    line-height: 1.3;
    color: var(--ink);
  }
  .info-table {
    position: absolute;
    left: 0;
    top: 219px;
    display: grid;
    grid-template-columns: 417px 397px 420px;
    grid-template-rows: 73px 149px 147px 147px;
    gap: 3px;
    background: var(--white);
  }
  .cell {
    box-sizing: border-box;
    color: var(--white);
    white-space: nowrap;
    overflow: hidden;
  }
  .section-title {
    background: var(--cyan);
    font-size: 33px;
    font-weight: 900;
    letter-spacing: 0.3px;
    display: flex;
    align-items: center;
    padding-left: 22px;
    padding-top: 4px;
  }
  .section-title.centered { padding-left: 24px; }
  .body-text {
    font-size: 19.5px;
    font-weight: 400;
    line-height: 33px;
    padding: 17px 0 0 22px;
  }
  .row-orange { background: var(--orange); }
  .row-cyan { background: var(--cyan); }
  .row-lime { background: var(--lime); }
  .footer-band {
    position: absolute;
    left: 0;
    bottom: 0;
    width: 1200px;
    height: 51px;
    background: var(--ink);
  }
</style>
</head>
<body>
<main class="slide">
  <h1 class="content-title">CONTENT TITLE HERE</h1>

  <div class="brand">
    <div class="brand-name"><span class="brand-square"></span>LUMOTEX</div>
    <div class="brand-tagline">YOUR TAGLINE<br>GOES HERE</div>
  </div>

  <section class="info-table">
    <div class="cell section-title">SECTION TITLE HERE</div>
    <div class="cell section-title centered">SECTION TITLE HERE</div>
    <div class="cell section-title">SECTION TITLE HERE</div>

    <div class="cell body-text row-orange">Lemon drops oat cake oat cake sugar<br>plum sweet gingerbread chocolate cake<br>gingerbread. Lemon drops oat cake oat</div>
    <div class="cell body-text row-orange">Lemon drops oat cake oat cake sugar<br>plum sweet gingerbread chocolate cake<br>gingerbread. Lemon drops oat cake oat</div>
    <div class="cell body-text row-orange">Lemon drops oat cake oat cake sugar<br>plum sweet gingerbread chocolate cake<br>gingerbread. Lemon drops oat cake oat</div>

    <div class="cell body-text row-cyan">Lemon drops oat cake oat cake sugar<br>plum sweet gingerbread chocolate cake<br>gingerbread. Lemon drops oat cake oat</div>
    <div class="cell body-text row-cyan">Lemon drops oat cake oat cake sugar<br>plum sweet gingerbread chocolate cake<br>gingerbread. Lemon drops oat cake oat</div>
    <div class="cell body-text row-cyan">Lemon drops oat cake oat cake sugar<br>plum sweet gingerbread chocolate cake<br>gingerbread. Lemon drops oat cake oat</div>

    <div class="cell body-text row-lime">Lemon drops oat cake oat cake sugar<br>plum sweet gingerbread chocolate cake<br>gingerbread. Lemon drops oat cake oat</div>
    <div class="cell body-text row-lime">Lemon drops oat cake oat cake sugar<br>plum sweet gingerbread chocolate cake<br>gingerbread. Lemon drops oat cake oat</div>
    <div class="cell body-text row-lime">Lemon drops oat cake oat cake sugar<br>plum sweet gingerbread chocolate cake<br>gingerbread. Lemon drops oat cake oat</div>
  </section>

  <footer class="footer-band"></footer>
</main>
</body>
</html>
```